you will use Ai to Copy the website Brivanta.com to come up with the basic frame work and it will give you the understanding of how I would like Kelbrava.com to be like. Kelbrava.com is a peer to peer rv rental site very similar to both of the other rv rental sites the difference is that are commission based 20% and above per rental and we will be one flat monthly rate and they keep all the earnings. Below is photo that will help you with the color scheme and the look and feel of the design

1 page

```html
<!DOCTYPE html>
<html lang="en">
<head>
<meta charset="utf-8">
<title>Kelbrava.com — The smart way to rent an RV</title>
<link href="https://fonts.googleapis.com/css2?family=Jost:wght@400;500;600;700&display=swap" rel="stylesheet">
<style>
:root{
  --navy:#0e1c40;
  --navy-deep:#0b1733;
  --green:#3f6c1f;
  --green-dark:#335a17;
  --ink:#1c1f2a;
  --muted:#3c4150;
  --soft-bg:#f6f7f6;
  --owner-bg:#f0f2ee;
  --line:#e3e5e8;
  --white:#ffffff;
}
*{box-sizing:border-box;margin:0;padding:0}
html,body{width:1200px;height:3002px;overflow:hidden}
body{position:relative;font-family:"Jost",Arial,sans-serif;color:var(--ink);background:var(--white)}
a{color:inherit;text-decoration:none}
.abs{position:absolute}

/* Header */
.site-header{position:absolute;left:0;top:0;width:1200px;height:90px;background:var(--navy);display:flex;align-items:center;padding:0 34px}
.brand{display:flex;align-items:center;gap:10px;color:var(--white);font-size:32px;font-weight:600;letter-spacing:.2px}
.brand-dot{width:14px;height:14px;border-radius:50%;background:var(--green)}
.main-nav{margin-left:auto;display:flex;align-items:center;gap:39px;color:var(--white);font-size:16px;font-weight:500}
.btn-outline-light{border:1.5px solid #c9cfdb;border-radius:6px;padding:9px 20px}

/* Hero */
.hero{position:absolute;left:0;top:90px;width:1200px;height:420px;background:linear-gradient(90deg,#2e3a2c 0%,#4b5b48 30%,#7d8f96 55%,#a9b7c0 75%,#3d4a3a 100%)}
.hero-title{position:absolute;left:83px;top:82px;font-size:70px;line-height:76px;font-weight:600;color:var(--white)}
.hero-sub{position:absolute;left:83px;top:234px;font-size:21px;line-height:31px;font-weight:500;color:var(--white)}
.search-box{position:absolute;left:83px;top:458px;width:1033px;height:99px;background:var(--white);border-radius:10px;box-shadow:0 6px 22px rgba(0,0,0,.14);display:flex;align-items:center;padding:0 26px}
.field{height:56px;padding-right:18px;border-right:1px solid var(--line);margin-right:22px}
.field-label{font-size:13.5px;color:var(--ink);margin-bottom:8px}
.field-value{font-size:13px;color:#8a8f99;display:flex;align-items:center;gap:6px}
.btn-search{margin-left:auto;background:var(--green);color:var(--white);font-size:17px;font-weight:500;border-radius:6px;width:136px;height:46px;display:flex;align-items:center;justify-content:center}

/* Section headings */
.section-title{position:absolute;left:0;width:1200px;text-align:center;font-size:28px;font-weight:500;color:var(--ink)}
.section-sub{position:absolute;left:0;width:1200px;text-align:center;font-size:17px;color:var(--muted)}

/* Why */
.feature{position:absolute;top:700px;width:270px;text-align:center}
.feature svg{display:block;margin:0 auto}
.feature-title{margin-top:30px;font-size:15.5px;font-weight:600}
.feature-text{margin-top:17px;font-size:14.5px;line-height:23.5px;color:var(--muted)}

/* Destinations */
.destinations{position:absolute;left:0;top:938px;width:1200px;height:600px;background:var(--soft-bg)}
.dest-card{position:absolute;top:128px;width:246px;text-align:center}
.dest-photo{width:246px;height:262px;border-radius:8px}
.dest-name{margin-top:14px;font-size:16.5px;font-weight:600}
.dest-text{margin-top:7px;font-size:14.5px;line-height:23px;color:var(--muted)}
.btn-outline{position:absolute;left:455px;top:525px;width:244px;height:43px;border:1.5px solid #4a4c8a;border-radius:6px;display:flex;align-items:center;justify-content:center;font-size:15.5px;font-weight:500;color:#2a2d5c;background:var(--white)}

/* Owners */
.owners{position:absolute;left:0;top:1538px;width:1200px;height:495px;background:var(--owner-bg)}
.owners-title{position:absolute;left:98px;top:60px;font-size:28px;line-height:34px;font-weight:500}
.owners-text{position:absolute;left:98px;top:135px;width:400px;font-size:16px;line-height:26.5px;color:var(--muted)}
.check-list{position:absolute;left:98px;top:236px;list-style:none}
.check-list li{display:flex;align-items:center;gap:16px;font-size:15.5px;height:36px}
.btn-green{position:absolute;left:98px;top:401px;width:147px;height:42px;background:var(--green);color:var(--white);border-radius:5px;font-size:16px;font-weight:500;display:flex;align-items:center;justify-content:center}
.owners-photo{position:absolute;left:565px;top:46px;width:542px;height:402px;border-radius:10px;background:linear-gradient(135deg,#3b4a2e 0%,#8a7a4e 45%,#d9b872 60%,#4a4a3c 100%)}

/* Reviews */
.review-card{position:absolute;top:2159px;width:310px;height:183px;background:var(--white);border-radius:8px;box-shadow:0 2px 12px rgba(0,0,0,.08);padding:22px 30px}
.stars{display:flex;gap:5px}
.review-text{margin-top:12px;font-size:14.5px;line-height:24.5px;color:var(--muted)}
.review-name{margin-top:13px;font-size:14.5px;color:var(--muted)}

/* App band */
.app-band{position:absolute;left:0;top:2396px;width:1200px;height:321px;background:var(--navy)}
.app-title{position:absolute;left:124px;top:87px;font-size:27px;font-weight:500;color:var(--white)}
.app-sub{position:absolute;left:124px;top:129px;font-size:16.5px;color:#dde2ec}
.store-badge{position:absolute;top:179px;height:53px;border-radius:6px;background:#000;border:1.5px solid #8b93a6}
.phones{position:absolute;left:650px;top:2377px;width:373px;height:340px;border-radius:24px 24px 0 0;background:linear-gradient(160deg,#f2f2f2 0%,#c9ccd1 50%,#2b3550 100%)}

/* Footer */
.site-footer{position:absolute;left:0;top:2717px;width:1200px;height:285px;background:var(--navy-deep);color:var(--white)}
.footer-brand{position:absolute;left:73px;top:25px;font-size:30px;font-weight:600;display:flex;align-items:center;gap:9px}
.footer-about{position:absolute;left:73px;top:92px;width:240px;font-size:12.5px;line-height:20px;color:#d3d8e3}
.socials{position:absolute;left:80px;top:180px;display:flex;gap:18px}
.socials span{width:24px;height:24px;border-radius:50%;background:#dfe3ec}
.footer-col{position:absolute;top:48px}
.footer-col h4{font-size:15.5px;font-weight:500;margin-bottom:10px}
.footer-col li{list-style:none;font-size:13.5px;line-height:26.5px;color:#d3d8e3}
.copyright{position:absolute;left:0;top:250px;width:1200px;text-align:center;font-size:14.5px;color:#d3d8e3}
</style>
</head>
<body>

<header class="site-header">
  <a class="brand" href="#"><span class="brand-dot"></span>Kelbrava.com</a>
  <nav class="main-nav">
    <a href="#">How It Works</a>
    <a href="#">Find an RV</a>
    <a href="#">List Your RV</a>
    <a href="#">Help</a>
    <a href="#">Login</a>
    <a href="#" class="btn-outline-light">Sign Up</a>
  </nav>
</header>

<section class="hero" role="img" aria-label="Motorhome parked by a mountain lake among pine trees">
  <h1 class="hero-title">The smart way<br>to rent an RV.</h1>
  <p class="hero-sub">Rent the perfect RV from local owners<br>and start your adventure today.</p>
</section>

<form class="search-box">
  <div class="field" style="width:276px">
    <div class="field-label">Pick up location</div>
    <div class="field-value"><svg width="12" height="14" viewBox="0 0 12 14"><path d="M6 1a4 4 0 0 1 4 4c0 3-4 8-4 8S2 8 2 5a4 4 0 0 1 4-4z" fill="none" stroke="#8a8f99" stroke-width="1.3"/><circle cx="6" cy="5" r="1.4" fill="#8a8f99"/></svg>Search city or airport</div>
  </div>
  <div class="field" style="width:163px">
    <div class="field-label">Pick up</div>
    <div class="field-value">Add dates</div>
  </div>
  <div class="field" style="width:165px">
    <div class="field-label">Drop off</div>
    <div class="field-value">Add dates</div>
  </div>
  <div class="field" style="width:186px">
    <div class="field-label">Guests</div>
    <div class="field-value">Add guests</div>
  </div>
  <a class="btn-search" href="#">Search</a>
</form>

<h2 class="section-title" style="top:598px">Why Kelbrava.com?</h2>
<p class="section-sub" style="top:641px">A better way to RV.</p>

<div class="feature" style="left:63px">
  <svg width="66" height="66" viewBox="0 0 66 66"><circle cx="33" cy="33" r="29" fill="none" stroke="var(--green)" stroke-width="4"/><text x="33" y="44" text-anchor="middle" font-family="Jost,sans-serif" font-size="32" font-weight="600" fill="var(--green)">$</text></svg>
  <div class="feature-title">Keep More, Earn More</div>
  <p class="feature-text">Only 20% commission<br>or a flat monthly rate.<br>You keep all the earnings.</p>
</div>
<div class="feature" style="left:332px">
  <svg width="72" height="66" viewBox="0 0 72 66" fill="none" stroke="var(--ink)" stroke-width="2.6"><circle cx="36" cy="16" r="9"/><circle cx="15" cy="22" r="7"/><circle cx="57" cy="22" r="7"/><path d="M20 56v-6a16 16 0 0 1 32 0v6z"/><path d="M4 52v-3a11 11 0 0 1 15-10"/><path d="M68 52v-3a11 11 0 0 0-15-10"/></svg>
  <div class="feature-title">Peer to Peer</div>
  <p class="feature-text">Rent directly from local<br>owners. More options,<br>better prices.</p>
</div>
<div class="feature" style="left:598px">
  <svg width="60" height="66" viewBox="0 0 60 66" fill="none" stroke="var(--ink)" stroke-width="2.6"><path d="M30 3l24 9v18c0 16-11 27-24 33C17 57 6 46 6 30V12z"/><circle cx="30" cy="32" r="11"/><path d="M23 39l14-14"/></svg>
  <div class="feature-title">Safe &amp; Secure</div>
  <p class="feature-text">We verify owners and<br>RVs, and provide 24/7<br>roadside assistance.</p>
</div>
<div class="feature" style="left:870px">
  <svg width="66" height="66" viewBox="0 0 66 66" fill="none" stroke="var(--ink)" stroke-width="2.6"><path d="M8 44V34a25 25 0 0 1 50 0v10"/><rect x="6" y="40" width="11" height="20" rx="4"/><rect x="49" y="40" width="11" height="20" rx="4"/></svg>
  <div class="feature-title">Support When You Need It</div>
  <p class="feature-text">Our team is here to help<br>before, during, and after<br>your trip.</p>
</div>

<section class="destinations">
  <h2 class="section-title" style="top:35px">Popular Destinations</h2>
  <p class="section-sub" style="top:77px">Discover amazing places to explore by RV.</p>

  <div class="dest-card" style="left:66px">
    <div class="dest-photo" role="img" aria-label="Motorhome in a red rock canyon" style="background:linear-gradient(180deg,#a9c3d9 0%,#b57a52 40%,#8a4e32 100%)"></div>
    <div class="dest-name">Grand Canyon, AZ</div>
    <p class="dest-text">Explore the natural wonder<br>of the world.</p>
  </div>
  <div class="dest-card" style="left:338px">
    <div class="dest-photo" role="img" aria-label="Mountain lake with pine forest and campers" style="background:linear-gradient(180deg,#8fb4d6 0%,#9aa6ad 30%,#2f5a3a 60%,#3a8a8e 80%,#4a5a34 100%)"></div>
    <div class="dest-name">Yellowstone, WY</div>
    <p class="dest-text">Geysers, wildlife, and wide<br>open spaces.</p>
  </div>
  <div class="dest-card" style="left:611px">
    <div class="dest-photo" role="img" aria-label="RV on a sandy beach with palm trees" style="background:linear-gradient(180deg,#5d9fd6 0%,#a8d0ea 45%,#5bb5c2 62%,#e6d3ad 80%,#d9c39a 100%)"></div>
    <div class="dest-name">Florida Keys, FL</div>
    <p class="dest-text">Sun, sand, and unforgettable<br>sunsets.</p>
  </div>
  <div class="dest-card" style="left:884px">
    <div class="dest-photo" role="img" aria-label="Coastal highway winding along cliffs" style="background:linear-gradient(160deg,#9cc2e0 0%,#8a6a42 40%,#5b4a34 70%,#44484a 100%)"></div>
    <div class="dest-name">Pacific Coast Highway, CA</div>
    <p class="dest-text">Scenic views along the<br>iconic coastline.</p>
  </div>

  <a class="btn-outline" href="#">Explore More Destinations</a>
</section>

<section class="owners">
  <h2 class="owners-title">Own an RV?<br>Start earning today.</h2>
  <p class="owners-text">List your RV on Kelbrava.com and start earning with one of the lowest commission rates in the industry.</p>
  <ul class="check-list">
    <li><svg width="21" height="21" viewBox="0 0 21 21"><circle cx="10.5" cy="10.5" r="10.5" fill="var(--green)"/><path d="M6 11l3 3 6-6" fill="none" stroke="#fff" stroke-width="2.2"/></svg>Only 20% commission or flat monthly rate</li>
    <li><svg width="21" height="21" viewBox="0 0 21 21"><circle cx="10.5" cy="10.5" r="10.5" fill="var(--green)"/><path d="M6 11l3 3 6-6" fill="none" stroke="#fff" stroke-width="2.2"/></svg>You keep 100% of the earnings</li>
    <li><svg width="21" height="21" viewBox="0 0 21 21"><circle cx="10.5" cy="10.5" r="10.5" fill="var(--green)"/><path d="M6 11l3 3 6-6" fill="none" stroke="#fff" stroke-width="2.2"/></svg>We handle the marketing</li>
    <li><svg width="21" height="21" viewBox="0 0 21 21"><circle cx="10.5" cy="10.5" r="10.5" fill="var(--green)"/><path d="M6 11l3 3 6-6" fill="none" stroke="#fff" stroke-width="2.2"/></svg>Flexible booking options</li>
  </ul>
  <a class="btn-green" href="#">List Your RV</a>
  <div class="owners-photo" role="img" aria-label="Motorhome parked by a lake at sunset with campers in chairs"></div>
</section>

<h2 class="section-title" style="top:2063px">What Our Customers Are Saying</h2>
<p class="section-sub" style="top:2106px">Real reviews from real RV adventurers.</p>

<article class="review-card" style="left:94px">
  <div class="stars"><svg width="96" height="16" viewBox="0 0 96 16" fill="var(--green)"><polygon points="8,0 10,6 16,6 11,9.5 13,16 8,12 3,16 5,9.5 0,6 6,6"/><polygon transform="translate(20 0)" points="8,0 10,6 16,6 11,9.5 13,16 8,12 3,16 5,9.5 0,6 6,6"/><polygon transform="translate(40 0)" points="8,0 10,6 16,6 11,9.5 13,16 8,12 3,16 5,9.5 0,6 6,6"/><polygon transform="translate(60 0)" points="8,0 10,6 16,6 11,9.5 13,16 8,12 3,16 5,9.5 0,6 6,6"/><polygon transform="translate(80 0)" points="8,0 10,6 16,6 11,9.5 13,16 8,12 3,16 5,9.5 0,6 6,6"/></svg></div>
  <p class="review-text">“Renting through Kelbrava.com was easy and the RV was perfect for our family trip!”</p>
  <p class="review-name">– Sarah J.</p>
</article>
<article class="review-card" style="left:433px">
  <div class="stars"><svg width="96" height="16" viewBox="0 0 96 16" fill="var(--green)"><polygon points="8,0 10,6 16,6 11,9.5 13,16 8,12 3,16 5,9.5 0,6 6,6"/><polygon transform="translate(20 0)" points="8,0 10,6 16,6 11,9.5 13,16 8,12 3,16 5,9.5 0,6 6,6"/><polygon transform="translate(40 0)" points="8,0 10,6 16,6 11,9.5 13,16 8,12 3,16 5,9.5 0,6 6,6"/><polygon transform="translate(60 0)" points="8,0 10,6 16,6 11,9.5 13,16 8,12 3,16 5,9.5 0,6 6,6"/><polygon transform="translate(80 0)" points="8,0 10,6 16,6 11,9.5 13,16 8,12 3,16 5,9.5 0,6 6,6"/></svg></div>
  <p class="review-text">“Great experience! The owner was super friendly and the RV was exactly as described.”</p>
  <p class="review-name">– Mike T.</p>
</article>
<article class="review-card" style="left:774px">
  <div class="stars"><svg width="96" height="16" viewBox="0 0 96 16" fill="var(--green)"><polygon points="8,0 10,6 16,6 11,9.5 13,16 8,12 3,16 5,9.5 0,6 6,6"/><polygon transform="translate(20 0)" points="8,0 10,6 16,6 11,9.5 13,16 8,12 3,16 5,9.5 0,6 6,6"/><polygon transform="translate(40 0)" points="8,0 10,6 16,6 11,9.5 13,16 8,12 3,16 5,9.5 0,6 6,6"/><polygon transform="translate(60 0)" points="8,0 10,6 16,6 11,9.5 13,16 8,12 3,16 5,9.5 0,6 6,6"/><polygon transform="translate(80 0)" points="8,0 10,6 16,6 11,9.5 13,16 8,12 3,16 5,9.5 0,6 6,6"/></svg></div>
  <p class="review-text">“The best way to rent an RV. Affordable, easy, and unforgettable memories.”</p>
  <p class="review-name">– Lisa K.</p>
</article>

<section class="app-band">
  <h2 class="app-title">The Adventure Starts Here</h2>
  <p class="app-sub">Download the Kelbrava.com app and hit the road.</p>
  <span class="store-badge" style="left:121px;width:185px" aria-label="App store download"></span>
  <span class="store-badge" style="left:340px;width:187px" aria-label="App store download"></span>
</section>
<div class="phones" role="img" aria-label="Two smartphones showing the Kelbrava.com app with RV listings"></div>

<footer class="site-footer">
  <div class="footer-brand"><span class="brand-dot"></span>Kelbrava.com</div>
  <p class="footer-about">Kelbrava.com is a peer-to-peer RV rental marketplace with low commission rates and big opportunities.</p>
  <div class="socials"><span></span><span></span><span></span><span></span></div>

  <div class="footer-col" style="left:377px"><h4>Explore</h4><ul><li>How It Works</li><li>Find an RV</li><li>Destinations</li><li>Roadside Assistance</li><li>FAQs</li></ul></div>
  <div class="footer-col" style="left:572px"><h4>Company</h4><ul><li>About Us</li><li>Careers</li><li>Blog</li><li>Press</li><li>Contact Us</li></ul></div>
  <div class="footer-col" style="left:748px"><h4>For Owners</h4><ul><li>List Your RV</li><li>Owner Resources</li><li>Pricing</li><li>Success Stories</li></ul></div>
  <div class="footer-col" style="left:938px"><h4>Support</h4><ul><li>Help Center</li><li>Safety</li><li>Terms of Service</li><li>Privacy Policy</li></ul></div>

  <p class="copyright">© 2024 Kelbrava.com. All rights reserved.</p>
</footer>

</body>
</html>
```